Innovative cost reduction consultant needs to build a group of technical advisors

We need to share our message and compassion for developing cost reduction in the automotive industry. We create opportunities for immediate innovation, by developing cost reduction solutions across suppliers with related process. Attached is an existing Power Point, but it needs improvement. Most of all, a good compelling story, why experts should join us.

Target Market(s)

Automotive industry, supply chain management

Industry/Entity Type

Automotive

Font styles to use
Serif
Sans Serif

Requirements
Must have
• Better visual graphics. There are a few, but they are not as visually appearing as I would like. A graphic with data should have a better visual impact then the ones that I created. I would like to share the message, that I am providing a solution for the automotive industry. The goal is to reduce costs and improve supplier and OEM relationships. The objective is to do so by creating opportunities for immediate innovation, by developing cost reduction solutions across suppliers with related processes. This message may need a visual graphic, which is missing from the presentation.
Nice to have
• Challenge my story and presentation. Does this make sense to you, and what is your opinions of the subject. Or, a relevant news source to validate the story.
Should not have
• I have not decided on the name of the venture or logo. So, let's just use my name as the source or writer. Marcus Delby, Cost Reduction Specialist. Thanks,

```html
<!DOCTYPE html>
<html lang="en">
<head>
<meta charset="utf-8">
<title>Collaborating at an even greater level to achieve momentous cost reduction</title>
<link rel="stylesheet" href="https://fonts.googleapis.com/css2?family=Roboto+Condensed:wght@400;700&family=Arimo:wght@400;700&display=swap">
<style>
  :root{
    --blue-deep:#0a347f;
    --blue-mid:#1a56b0;
    --blue-band:#1f9be0;
    --table-head:#1e9be6;
    --ink:#1a1a1a;
    --grey-text:#555;
    --brown:#8a5a35;
    --brown-light:#b88a5f;
    --green:#1d9a3a;
    --green-dark:#137a2c;
    --c-red:#ef5a5a;
    --c-salmon:#f2876a;
    --c-orange:#f4ac6c;
    --c-yellow:#f1e57c;
    --c-lime:#c9df7a;
    --c-green-light:#9fd07d;
    --c-green:#52b56a;
    --c-green-dark:#1f7a2e;
    --c-tan:#b98a5e;
    --dot:#666;
  }
  *{margin:0;padding:0;box-sizing:border-box}
  html,body{width:1200px;height:650px;overflow:hidden;background:#fff}
  .canvas{position:relative;width:1200px;height:650px;overflow:hidden;
    background:linear-gradient(90deg,#fff 0%,#fff 55%,#d4d6d9 100%);
    font-family:"Roboto Condensed",Arial,sans-serif;color:var(--ink)}
  .hero{position:absolute;left:0;top:0;width:1200px;height:242px;
    background:linear-gradient(180deg,var(--blue-deep) 0%,var(--blue-mid) 100%)}
  .hero__title{position:absolute;left:58px;top:38px;font-weight:700;font-size:67px;line-height:78px;
    letter-spacing:.3px;
    background:linear-gradient(180deg,#ffffff 0%,#e9ecef 45%,#a8adb3 100%);
    -webkit-background-clip:text;background-clip:text;color:transparent;
    filter:drop-shadow(2px 3px 2px rgba(0,0,0,.55))}
  .footer-band{position:absolute;left:0;bottom:0;width:1200px;height:28px;background:var(--blue-band)}

  .survey-label{position:absolute;left:60px;top:334px;width:31px;height:216px;
    border:2px dotted var(--dot);border-radius:8px;display:flex;align-items:center;justify-content:center;background:#fff}
  .survey-label span{transform:rotate(-90deg);white-space:nowrap;font-weight:700;font-size:22px;color:#222}
  .connectors{position:absolute;left:0;top:0}

  .survey-frame{position:absolute;left:121px;top:271px;width:494px;height:318px;border:1.5px dotted var(--dot)}
  .survey-table{position:absolute;left:129px;top:278px;width:479px;border-collapse:collapse;table-layout:fixed;
    font-family:Arimo,Arial,sans-serif;font-size:11.5px}
  .survey-table th{background:var(--table-head);height:33px;font-weight:700;font-size:12.5px;border:1.5px solid #111}
  .survey-table td{height:18px;text-align:right;padding-right:4px;border:1px solid #222;border-top:none;border-bottom:1px solid #999;background:#fff}
  .survey-table tr.tall td{height:30px;vertical-align:bottom}
  .survey-table tbody tr:last-child td{border-bottom:1.5px solid #111}
  .red{background:var(--c-red)!important}.salmon{background:var(--c-salmon)!important}
  .orange{background:var(--c-orange)!important}.yellow{background:var(--c-yellow)!important}
  .lime{background:var(--c-lime)!important}.green-light{background:var(--c-green-light)!important}
  .green{background:var(--c-green)!important}.green-dark{background:var(--c-green-dark)!important}
  .tan{background:var(--c-tan)!important}
  .tan-fade{background:linear-gradient(90deg,var(--c-tan),#8c6a4a)!important}
  .legend{position:absolute;left:382px;top:590px;width:226px;text-align:right;font-family:Arimo,Arial,sans-serif;font-size:9.5px;color:#333}

  .tab{position:absolute;height:32px;border-radius:6px;color:#fff;font-size:20px;display:flex;align-items:center;justify-content:center;
    background:linear-gradient(90deg,var(--brown) 0%,var(--brown-light) 100%)}
  .tab--drivers{left:696px;top:274px;width:145px}
  .tab--result{left:884px;top:274px;width:135px}
  .note-box{position:absolute;border:1.5px dotted #8a6a4d;border-radius:8px;background:#fff;padding:0 0 0 12px}
  .note-box ul{list-style:none}
  .note-box li{font-size:13px;line-height:17px;color:#333;font-family:Arimo,Arial,sans-serif}
  .note-box li::before{content:"•";color:#c47a3c;margin-right:5px}
  .drivers-list{left:705px;top:306px;width:152px;height:84px;padding-top:10px}
  .result-list{left:892px;top:293px;width:153px;height:68px;padding-top:21px}

  .arrow{position:absolute;left:612px;top:408px}
  .question-box{position:absolute;left:834px;top:440px;width:305px;height:142px;border:1.5px dotted var(--dot);border-radius:10px;background:#fff;padding:20px 0 0 20px}
  .question-box li{list-style:none;font-size:15.5px;line-height:23px;color:#222;font-family:Arimo,Arial,sans-serif}
  .question-box li::before{content:"•";color:var(--blue-band);margin-right:7px;font-size:17px}
  .question-pill{position:absolute;left:771px;top:414px;width:337px;height:38px;border-radius:10px;background:#fff;
    box-shadow:0 0 0 1.5px #9a9a9a;display:flex;align-items:center;justify-content:center;
    font-weight:700;font-size:24px;color:var(--green)}
</style>
</head>
<body>
<main class="canvas">
  <header class="hero">
    <h1 class="hero__title">Collaborating at an even greater level<br>to achieve momentous cost reduction</h1>
  </header>

  <svg class="connectors" width="1200" height="650" aria-hidden="true">
    <g stroke="#666" stroke-width="1.3" stroke-dasharray="2 2" fill="none">
      <line x1="91" y1="350" x2="121" y2="350"/>
      <line x1="91" y1="530" x2="121" y2="530"/>
      <line x1="608" y1="324" x2="645" y2="324"/>
      <line x1="645" y1="324" x2="705" y2="324"/>
      <line x1="645" y1="341" x2="705" y2="341"/>
      <line x1="645" y1="357" x2="705" y2="357"/>
      <line x1="645" y1="375" x2="705" y2="375"/>
      <line x1="645" y1="324" x2="645" y2="375"/>
      <line x1="857" y1="333" x2="892" y2="333"/>
    </g>
  </svg>

  <div class="survey-label"><span>Supplier Survey</span></div>

  <div class="survey-frame"></div>
  <table class="survey-table">
    <thead><tr><th>Raw Material</th><th>Machine process</th><th>Assembly</th><th>Components</th></tr></thead>
    <tbody>
      <tr><td class="salmon">$5,000.00</td><td class="yellow">$10,000.00</td><td></td><td></td></tr>
      <tr><td></td><td></td><td></td><td></td></tr>
      <tr><td></td><td class="yellow">$13,410.00</td><td></td><td></td></tr>
      <tr class="tall"><td></td><td></td><td class="tan">$3,000.00</td><td class="tan-fade">$3,000.00</td></tr>
      <tr><td class="red">$3,740.00</td><td class="salmon">$3,740.00</td><td></td><td></td></tr>
      <tr><td class="green-light">$71,500.00</td><td class="green">$55,000.00</td><td></td><td class="green-dark">$68,000.00</td></tr>
      <tr><td></td><td></td><td class="yellow">$5,000.00</td><td class="yellow">$6,000.00</td></tr>
      <tr><td class="yellow">$25,000.00</td><td class="salmon">$14,000.00</td><td class="orange">$4,000.00</td><td class="yellow">$8,000.00</td></tr>
      <tr><td></td><td class="red">$400.00</td><td class="salmon">$2,200.00</td><td></td></tr>
      <tr><td></td><td class="salmon">$3,000.00</td><td></td><td class="salmon">$3,000.00</td></tr>
      <tr><td class="red">$3,000.00</td><td></td><td class="orange">$3,000.00</td><td></td></tr>
      <tr><td class="salmon">$5,000.00</td><td class="yellow">$13,000.00</td><td class="orange">$2,500.00</td><td class="lime">$20,000.00</td></tr>
      <tr><td></td><td></td><td class="salmon">$1,125.00</td><td></td></tr>
    </tbody>
  </table>
  <p class="legend">Red = poor effort • Green = best effort</p>

  <div class="note-box drivers-list"><ul><li>Capital</li><li>Technical</li><li>Resources</li><li>Event</li></ul></div>
  <div class="tab tab--drivers">Key Drivers</div>
  <div class="note-box result-list"><ul><li>Energy Savings</li><li>Productivity increase</li></ul></div>
  <div class="tab tab--result">Result</div>

  <svg class="arrow" width="170" height="52" viewBox="0 0 170 52" aria-hidden="true">
    <defs><linearGradient id="arrowFill" x1="0" y1="0" x2="0" y2="1">
      <stop offset="0" stop-color="#2fb04a"/><stop offset="1" stop-color="#137a2c"/></linearGradient></defs>
    <polygon points="0,26 34,0 34,16 170,16 170,36 34,36 34,52" fill="url(#arrowFill)"/>
  </svg>

  <ul class="question-box">
    <li>Minimal effort…What is missing?</li>
    <li>What separates best vs poor effort?</li>
    <li>Technical know how?</li>
    <li>Resources, manpower?</li>
    <li>An event, the right timing?</li>
  </ul>
  <div class="question-pill">How were they successful?</div>

  <div class="footer-band"></div>
</main>
</body>
</html>
```